Retail/Wholesale website graphic template

I need to design a new graphic template for a website for a client. The website will be a retail/wholesale company site with most pages dedicated to presentation. There will also be an online store and a blog. However, you don't need to worry about those. All I need from you is a graphic template for a generic site page.

It will need to include standard UI elements, in case I need those. I am attaching a more detailed assignment in .docx format.

The logo is also attached.

Target Market(s)

small business owners, (occasional) retail customers

Industry/Entity Type

Wholesale

Number of Pages Required

1 page

Font styles to use
Serif
Sans Serif

Colors
ec1f27
474747

Requirements
Must have
• must match logo, be clean, minimal and with slightly larger text size
Should not have
• must not be modern-looking where you have to scroll and scroll and scroll to get to the bottom of the homepage. most of my visitors are "old" people, they do not get this type of design.

```html
<!DOCTYPE html>
<html lang="en">
<head>
<meta charset="utf-8">
<title>Harbor Imports</title>
<link href="https://fonts.googleapis.com/css2?family=Montserrat:wght@400;600;700&family=Open+Sans:wght@400;600;700&display=swap" rel="stylesheet">
<style>
:root{
  --red:#ec1f27;
  --ink:#474747;
  --dark:#222222;
  --text:#6a6a6a;
  --line:#cfcfcf;
  --footer:#262626;
  --footer-text:#e2e2e2;
  --white:#ffffff;
}
*{margin:0;padding:0;box-sizing:border-box}
html,body{width:1200px;height:3285px;overflow:hidden}
body{position:relative;background:var(--white);font-family:"Open Sans",Arial,sans-serif;color:var(--ink)}
.abs{position:absolute}
/* header */
.brand{left:99px;top:22px;height:68px;display:flex;align-items:center;font-family:"Montserrat",Arial,sans-serif;font-weight:700;font-size:22px;letter-spacing:1px;color:var(--dark);white-space:nowrap}
.brand-square{width:16px;height:16px;background:var(--red);margin-right:12px;flex:none}
.topbar{right:99px;top:24px;display:flex;align-items:center;gap:12px;font-size:14px;font-weight:600;color:var(--dark)}
.topbar svg{width:14px;height:14px;fill:var(--red);margin-right:6px;vertical-align:-2px}
.nav{right:99px;top:70px;display:flex;gap:24px;align-items:center;font-family:"Montserrat",Arial,sans-serif;font-weight:600;font-size:13.5px;color:var(--dark);white-space:nowrap}
.nav .active{color:var(--red)}
.nav svg{width:15px;height:15px}
/* hero */
.hero{left:0;top:110px;width:1200px;height:562px;background:linear-gradient(135deg,#6b6660 0%,#4a4744 40%,#8a8580 70%,#3c3a38 100%)}
.hero-shade{left:0;top:110px;width:1200px;height:562px;background:rgba(0,0,0,.25)}
.hero-box{left:171px;top:307px;width:858px;height:151px;border:2px solid var(--white)}
.hero-title{left:0;top:316px;width:1200px;text-align:center;font-family:"Montserrat",Arial,sans-serif;font-weight:600;font-size:90px;color:var(--white);letter-spacing:1px;white-space:nowrap}
.hero-sub{left:283px;top:438px;width:634px;text-align:center;font-size:28px;color:var(--white)}
.hero-sub span{padding:0 14px;background:rgba(70,66,62,1)}
.arrow{width:44px;height:60px;background:rgba(0,0,0,.4);display:flex;align-items:center;justify-content:center}
.arrow svg{width:18px;height:26px;stroke:var(--white);fill:none;stroke-width:3}
/* section headings */
.heading{border:2px solid var(--dark);text-align:center;font-family:"Montserrat",Arial,sans-serif}
.heading .big{display:block;font-weight:700;font-size:34px;color:var(--dark);line-height:1;padding-top:14px}
.heading .small{position:absolute;left:50%;bottom:-14px;transform:translateX(-50%);white-space:nowrap;background:var(--white);padding:0 14px;font-weight:600;font-size:22px;color:var(--red);line-height:26px}
.heading.light{border-color:var(--white)}
.heading.light .big{color:var(--white)}
.heading.light .small{color:var(--white);background:#3b3633}
.welcome-text{left:180px;top:883px;width:840px;text-align:center;font-size:14px;line-height:29.5px;color:var(--text)}
.btn{display:flex;align-items:center;justify-content:center;background:var(--red);color:var(--white);border-radius:30px;font-weight:700;font-size:16px}
/* products */
.products{left:0;top:1270px;width:1200px;height:558px;background:radial-gradient(ellipse at 50% 55%,#8a7d72 0%,#4d433c 55%,#2c2622 100%)}
.circle{width:236px;height:236px;border-radius:50%;border:4px solid var(--white);overflow:hidden}
.circle .ph{width:100%;height:100%}
.circle .label{position:absolute;left:0;top:140px;width:100%;height:48px;background:rgba(0,0,0,.7);color:var(--white);font-family:"Montserrat",Arial,sans-serif;font-weight:600;font-size:18px;display:flex;align-items:center;justify-content:center}
.p-arrow svg{width:20px;height:30px;stroke:var(--white);fill:none;stroke-width:3.5}
/* why */
.why-intro{left:99px;top:2058px;width:510px;font-size:15px;line-height:27px;color:var(--text)}
.ticks{left:99px;top:2142px;width:540px;list-style:none}
.ticks li{display:flex;align-items:center;height:29px;font-size:14.5px;color:var(--text)}
.ticks svg{width:16px;height:16px;margin-right:16px;flex:none}
.why-photo{left:653px;top:1931px;width:448px;height:449px;background:linear-gradient(160deg,#c9d3dc 0%,#8f9aa4 45%,#9a6a45 75%,#c8a47a 100%)}
.divider{left:99px;top:2478px;width:1002px;height:2px;background:var(--line)}
/* partners */
.badge{top:2722px;width:186px;height:96px;border:1px solid #d8d8d8;background:var(--white);display:flex;align-items:center;justify-content:center}
.badge i{display:block;width:120px;height:30px;border-radius:4px;background:#c2c2c2}
.badge.featured{top:2709px;left:484px;width:232px;height:120px;box-shadow:0 0 10px rgba(0,0,0,.15)}
.badge.featured i{background:linear-gradient(90deg,#7cbf3c,#1f6fb2)}
/* footer */
.footer-rule{left:0;top:2919px;width:1200px;height:6px;background:var(--red)}
.footer{left:0;top:2925px;width:1200px;height:360px;background:var(--footer)}
.foot-brand{left:99px;top:3066px;display:flex;align-items:center;font-family:"Montserrat",Arial,sans-serif;font-weight:700;font-size:22px;letter-spacing:1px;color:var(--white);white-space:nowrap}
.foot-brand .brand-square{background:var(--white)}
.col{color:var(--white)}
.col h4{font-family:"Montserrat",Arial,sans-serif;font-weight:600;font-size:18px;margin-bottom:16px;color:var(--white)}
.col ul{list-style:none}
.col li{font-size:12.5px;line-height:21px;color:var(--footer-text)}
.col.links li{line-height:26px}
.col.spaced li{line-height:30px}
.contact li{display:flex;align-items:flex-start;gap:18px;margin-bottom:12px;line-height:18px}
.contact svg{width:14px;height:14px;fill:var(--white);flex:none;margin-top:2px}
.foot-line{left:99px;top:3206px;width:1002px;height:1px;background:#444}
.copy{left:99px;top:3235px;font-size:12px;color:var(--footer-text)}
.social{left:976px;top:3230px;display:flex;gap:10px}
.social span{width:26px;height:26px;border-radius:50%;border:1px solid #bdbdbd;display:block}
</style>
</head>
<body>

<header>
  <div class="abs brand"><span class="brand-square"></span>HARBOR IMPORTS</div>
  <div class="abs topbar">
    <span><svg viewBox="0 0 24 24"><path d="M6.6 10.8a15 15 0 006.6 6.6l2.2-2.2a1 1 0 011-.25 11 11 0 003.6.6 1 1 0 011 1V20a1 1 0 01-1 1A17 17 0 013 4a1 1 0 011-1h3.5a1 1 0 011 1 11 11 0 00.6 3.6 1 1 0 01-.25 1z"/></svg>1 888 888 8888</span>
    <span>|</span>
    <span><svg viewBox="0 0 24 24"><path d="M2 5h20v2l-10 6L2 7zm0 4l10 6 10-6v10H2z"/></svg>info@harborimports.com</span>
    <span>|</span>
    <span><svg viewBox="0 0 24 24"><circle cx="12" cy="7" r="5"/><path d="M2 22c0-6 5-9 10-9s10 3 10 9z"/></svg>My Account</span>
  </div>
  <nav class="abs nav">
    <span class="active">HOME</span><span>ABOUT</span><span>PRODUCTS</span><span>PROCESS</span><span>DISTRIBUTION</span><span>PARTNERS</span><span>CONTACT</span>
    <svg viewBox="0 0 24 24" fill="none" stroke="#222" stroke-width="3"><circle cx="10" cy="10" r="7"/><path d="M15 15l7 7"/></svg>
  </nav>
</header>

<section>
  <div class="abs hero" role="img" aria-label="Market display of seafood in white trays with price tags"></div>
  <div class="abs hero-shade"></div>
  <div class="abs hero-box"></div>
  <h1 class="abs hero-title">HARBOR IMPORTS</h1>
  <p class="abs hero-sub"><span>We are a retail &amp; whole sale import company</span></p>
  <div class="abs arrow" style="left:0;top:360px"><svg viewBox="0 0 18 26"><path d="M14 3L4 13l10 10"/></svg></div>
  <div class="abs arrow" style="left:1156px;top:360px"><svg viewBox="0 0 18 26"><path d="M4 3l10 10L4 23"/></svg></div>
</section>

<section>
  <div class="abs heading" style="left:462px;top:753px;width:276px;height:81px"><span class="big">WELCOME TO</span><span class="small">HARBOR IMPORTS</span></div>
  <p class="abs welcome-text">Nemo enim ipsam voluptatem quia voluptas sit aspernatur aut odit aut fugit, sed quia consequuntur magni dolores eos qui ratione voluptatem sequi nesciunt. Neque porro quisquam est, qui dolorem ipsum quia dolor sit amet, consectetur, adipisci velit, sed quia non numquam eius modi tempora incidunt ut labore et dolore magnam aliquam quaerat voluptatem. Ut enim ad minima veniam, quis nostrum exercitationem ullam corporis suscipit laboriosam, nisi ut aliquid ex ea commodi consequatur? Quis autem vel eum iure reprehenderit qui in libero tempore, cum soluta nobis est eligendi optio cumque nihil impeditoliore m quo minus id quod maxime placeat facere possimus.</p>
  <div class="abs btn" style="left:517px;top:1101px;width:168px;height:59px">READ MORE</div>
</section>

<section>
  <div class="abs products" role="img" aria-label="Close-up of white rice grains in a dark bowl"></div>
  <div class="abs heading light" style="left:486px;top:1355px;width:228px;height:80px"><span class="big">OUR</span><span class="small">PRODUCTS</span></div>
  <div class="abs p-arrow" style="left:34px;top:1597px"><svg viewBox="0 0 20 30"><path d="M16 3L5 15l11 12"/></svg></div>
  <div class="abs p-arrow" style="left:1144px;top:1597px"><svg viewBox="0 0 20 30"><path d="M4 3l11 12L4 27"/></svg></div>
  <div class="abs circle" style="left:101px;top:1494px"><div class="ph" role="img" aria-label="Grocery store aisle with shelves of goods" style="background:linear-gradient(180deg,#b9bcc0,#6d7d52 60%,#8a5a3a)"></div><div class="label">Grocery</div></div>
  <div class="abs circle" style="left:355px;top:1494px"><div class="ph" role="img" aria-label="Fresh fish fillets on a deli counter" style="background:linear-gradient(180deg,#8c8e94,#d7c8c4 50%,#a9a6aa)"></div><div class="label">Meat, Seafood &amp; Deli</div></div>
  <div class="abs circle" style="left:607px;top:1494px"><div class="ph" role="img" aria-label="Glass jugs and jars of milk" style="background:linear-gradient(180deg,#9fa7ae,#eceae4 55%,#b9a58a)"></div><div class="label">Dairy</div></div>
  <div class="abs circle" style="left:861px;top:1494px"><div class="ph" role="img" aria-label="Stacks of white plates and bowls" style="background:linear-gradient(180deg,#5e6166,#e7e8ea 50%,#c5c7ca)"></div><div class="label">Tableware</div></div>
</section>

<section>
  <div class="abs heading" style="left:99px;top:1931px;width:276px;height:81px"><span class="big">WHY CHOOSE</span><span class="small">HARBOR IMPORTS</span></div>
  <p class="abs why-intro">At vero eos et accusamus et iusto odio dignissimos ducimus qui bla nditiis pra esentium voluptatum deleniti atque corrup.</p>
  <ul class="abs ticks">
    <li><svg viewBox="0 0 16 16"><circle cx="8" cy="8" r="8" fill="#ec1f27"/><path d="M4.5 8.2l2.3 2.3 4.7-4.7" stroke="#fff" stroke-width="2" fill="none"/></svg>At vero eos et accusamus et iusto odio dignissimoet voluptas ducimus</li>
    <li><svg viewBox="0 0 16 16"><circle cx="8" cy="8" r="8" fill="#ec1f27"/><path d="M4.5 8.2l2.3 2.3 4.7-4.7" stroke="#fff" stroke-width="2" fill="none"/></svg>Qui bla nditiis pra et voluptaesentium voluptatum deleniti atque corrup</li>
    <li><svg viewBox="0 0 16 16"><circle cx="8" cy="8" r="8" fill="#ec1f27"/><path d="M4.5 8.2l2.3 2.3 4.7-4.7" stroke="#fff" stroke-width="2" fill="none"/></svg>Nam libero tempore,et volupta cum soluta nobis est eligendi optio cum</li>
    <li><svg viewBox="0 0 16 16"><circle cx="8" cy="8" r="8" fill="#ec1f27"/><path d="M4.5 8.2l2.3 2.3 4.7-4.7" stroke="#fff" stroke-width="2" fill="none"/></svg>Omnis voluptas assuet voluptamenda est, omnis dolor repellenduser</li>
    <li><svg viewBox="0 0 16 16"><circle cx="8" cy="8" r="8" fill="#ec1f27"/><path d="M4.5 8.2l2.3 2.3 4.7-4.7" stroke="#fff" stroke-width="2" fill="none"/></svg>Itaque earum reruet voluptam hic tenetur a sapiente delectus iciendis vo</li>
  </ul>
  <div class="abs btn" style="left:99px;top:2326px;width:168px;height:59px">READ MORE</div>
  <div class="abs why-photo" role="img" aria-label="Two warehouse workers with a laptop checking stock on tall shelves"></div>
  <div class="abs divider"></div>
</section>

<section>
  <div class="abs heading" style="left:486px;top:2566px;width:228px;height:82px"><span class="big">OUR</span><span class="small">PARTNERS</span></div>
  <div class="abs badge" style="left:99px"><i></i></div>
  <div class="abs badge" style="left:302px"><i></i></div>
  <div class="abs badge featured"><i></i></div>
  <div class="abs badge" style="left:720px"><i></i></div>
  <div class="abs badge" style="left:915px"><i></i></div>
</section>

<footer>
  <div class="abs footer-rule"></div>
  <div class="abs footer"></div>
  <div class="abs foot-brand"><span class="brand-square"></span>HARBOR IMPORTS</div>
  <div class="abs col" style="left:416px;top:2987px"><h4>Information</h4><ul><li>Home</li><li>About</li><li>Products</li><li>Process</li><li>Distribution</li><li>Partners</li><li>Contact</li></ul></div>
  <div class="abs col links" style="left:569px;top:2987px"><h4>Quick Links</h4><ul><li>About Us</li><li>Careers</li><li>Privacy &amp; Security</li><li>Site Map</li><li>Terms of Use</li><li>Blog</li></ul></div>
  <div class="abs col spaced" style="left:729px;top:2987px"><h4>My Account</h4><ul><li>Delivery Information</li><li>My Account</li><li>Order Tracking</li><li>Reminder Service</li><li>Shipping, Returns &amp; Fees</li></ul></div>
  <div class="abs col contact" style="left:898px;top:2987px"><h4>Contact Us</h4><ul>
    <li><svg viewBox="0 0 24 24"><path d="M12 2a7 7 0 00-7 7c0 5 7 13 7 13s7-8 7-13a7 7 0 00-7-7zm0 9.5A2.5 2.5 0 1112 6a2.5 2.5 0 010 5.5z"/></svg><span>Suite 5, 210 Bay Road Harbourside<br>Western Australia 6010</span></li>
    <li><svg viewBox="0 0 24 24"><path d="M6.6 10.8a15 15 0 006.6 6.6l2.2-2.2a1 1 0 011-.25 11 11 0 003.6.6 1 1 0 011 1V20a1 1 0 01-1 1A17 17 0 013 4a1 1 0 011-1h3.5a1 1 0 011 1 11 11 0 00.6 3.6 1 1 0 01-.25 1z"/></svg><span>1 888 888 8888</span></li>
    <li><svg viewBox="0 0 24 24"><path d="M6 2h10v6H6zM3 9h18v11H3zm4 3v2h3v-2zm5 0v2h3v-2zm-5 4v2h3v-2zm5 0v2h3v-2z"/></svg><span>1 222 222 2222</span></li>
    <li><svg viewBox="0 0 24 24"><path d="M2 5h20v2l-10 6L2 7zm0 4l10 6 10-6v10H2z"/></svg><span>info@harborimports.com</span></li>
  </ul></div>
  <div class="abs foot-line"></div>
  <p class="abs copy">Copyrights © 2018, Harbor Imports . All rights reserved.</p>
  <div class="abs social"><span></span><span></span><span></span><span></span></div>
</footer>

</body>
</html>
```